RW Framewell Inc Business cards

We need business cards using our existing logo but slightly modified. Right now the logo says RW Loadbearing Masonry. We want to keep the RW part of the design, but replace the Structural Concrete portion with "FRAMEWELL". Please see the attached file.
Ideally this would be a blank template so we can add Different Names, titles, and phone numbers later.
On the one side we want only the logo and on the other side the detail. I'm attaching an example for you to see.
Please reach out with any other questions. Our address and other details will be given out once we find a design we like.

Target Market(s)

Construction Industry

```html
<!DOCTYPE html>
<html lang="en">
<head>
<meta charset="utf-8">
<title>RW Framewell Inc Business Cards</title>
<link href="https://fonts.googleapis.com/css2?family=Montserrat:wght@600&family=Roboto:wght@400;500&display=swap" rel="stylesheet">
<style>
  :root {
    --bg: #c9c9c9;
    --card: #fbfbfb;
    --brand-blue: #2d5fa8;
    --brand-grey: #6b6b6b;
    --text-grey: #5a5a5a;
  }
  * { box-sizing: border-box; margin: 0; padding: 0; }
  html, body { width: 1200px; height: 852px; overflow: hidden; }
  body {
    background: var(--bg);
    font-family: "Roboto", Arial, sans-serif;
    position: relative;
  }
  .card {
    position: absolute;
    width: 520px;
    height: 297px;
    background: var(--card);
    border-radius: 18px;
    overflow: hidden;
    box-shadow: 0 6px 18px rgba(0,0,0,0.18);
  }
  .card--front { left: 60px; top: 278px; }
  .card--back { left: 620px; top: 278px; }

  .wordmark {
    font-family: "Montserrat", Arial, sans-serif;
    font-weight: 600;
    color: var(--brand-blue);
    letter-spacing: 3px;
    white-space: nowrap;
  }
  .card--front .wordmark {
    position: absolute;
    left: 0; right: 0; top: 122px;
    text-align: center;
    font-size: 34px;
  }
  .edge-band {
    position: absolute;
    left: 0; right: 0; bottom: 0;
    height: 12px;
    display: flex;
  }
  .edge-band__grey { flex: 0 0 42%; background: var(--brand-grey); }
  .edge-band__blue { flex: 1; background: var(--brand-blue); }

  .card--back .wordmark {
    position: absolute;
    left: 34px; top: 130px;
    font-size: 24px;
  }
  .contact {
    position: absolute;
    left: 292px; top: 72px;
    color: var(--text-grey);
    font-size: 13px;
    line-height: 1.45;
  }
  .contact__name {
    color: var(--brand-blue);
    font-weight: 500;
    font-size: 19px;
  }
  .contact__title { margin-bottom: 14px; }
  .contact__row { display: flex; align-items: center; gap: 9px; }
  .contact__row svg { width: 11px; height: 11px; fill: var(--brand-blue); flex: none; }
  .contact__address { margin-top: 6px; padding-left: 20px; }
</style>
</head>
<body>
  <section class="card card--front">
    <div class="wordmark">RW FRAMEWELL</div>
    <div class="edge-band">
      <div class="edge-band__grey"></div>
      <div class="edge-band__blue"></div>
    </div>
  </section>

  <section class="card card--back">
    <div class="wordmark">RW FRAMEWELL</div>
    <div class="contact">
      <div class="contact__name">Daniel RW Harlow</div>
      <div class="contact__title">Managing Director</div>
      <div class="contact__row">
        <svg viewBox="0 0 12 12" aria-hidden="true"><path d="M2.5 1h2l1 3-1.3 1a7 7 0 0 0 2.8 2.8L8 6.5l3 1v2A1.5 1.5 0 0 1 9.5 11 8.5 8.5 0 0 1 1 2.5 1.5 1.5 0 0 1 2.5 1z"/></svg>
        <span>555-014-2290</span>
      </div>
      <div class="contact__row">
        <svg viewBox="0 0 12 12" aria-hidden="true"><path d="M1 2.5h10v7H1z M1 2.5l5 4 5-4" fill="none" stroke="#2d5fa8" stroke-width="1.2"/></svg>
        <span>daniel@framewellco.com</span>
      </div>
      <div class="contact__row">
        <svg viewBox="0 0 12 12" aria-hidden="true"><circle cx="6" cy="6" r="5"/></svg>
        <span>www.framewellco.com</span>
      </div>
      <div class="contact__address">418 Beam Ave., Oakridge,<br>California, US 905512</div>
    </div>
  </section>
</body>
</html>
```